Sleek modern site for stage hypnotist who does high school, college, university and corporate gigs.

Need a website design for stage hypnotist Gareth Munroe
I'm using a weebly domain

Gareth Munroe is a stage hypnotist who does high school shows , colleges, corporate and fundraisers
Looking for something sleek and modern looking.
I need about 4 pages at least one main describing what i do
1st page Describes what events i do (high school, college, corporate, weddings, fundraisers, fairs)
2nd page would be an about/bio page
3rd FAQ page about hypnosis.

*what venues do you work with?
*how long is your show?
*How do we promote the show?
*is it safe
*are you insured?
*how much does it cost?
4th page will be a contact page and link to my social media like Instagram, twitter, and possibly Facebook.

Included is a few pictures that I'll probably including on the site. I'm waiting on the rest for photoshoot at the this week. Some of these pictures probably will have different stock backgrounds other than grey (something like a las vegas strip or a stage.

Visually I'm looking for a cool color scheme.

Target Market(s)

High school for now but college and corporate down the road.

Industry/Entity Type

Entertainment Industry

Coding

Coded - Design and coding required

Number of Pages Required

4 page

Font styles to use
Serif
Sans Serif

Colors
3277b5
85acd3
9d9d9d
5c5c5c
cbcbcb
aaaaaa
1b1b1b
333333

Requirements
Must have
• MUST BE ABLE TO WORK WITH WEEBLY
• A sleek and professional look as if I've been doing this for years.
• The ability to edit the text of the site so i can improve upon the persuasive parts if need be.
• I also will be getting more promotional photos in the 5 or 6 days after the deadline days so if i pick your project i'd like to be able to integrate some of them into the design. The 3 photos i provided are somewhat place holders to give you an idea of the rest that are to come.
Nice to have
• drop down links
Should not have
• if you google other stage hypnotists their sites are a bit stale and not that modern.

```html
<!DOCTYPE html>
<html lang="en">
<head>
<meta charset="utf-8">
<title>Gareth Munroe — Stage Hypnotist</title>
<link rel="stylesheet" href="https://fonts.googleapis.com/css2?family=Fjalla+One&family=Montserrat:wght@500;700&family=PT+Sans:wght@400;700&family=Dancing+Script:wght@500&display=swap">
<style>
  :root {
    --ink-dark: #1b1b1b;
    --gold: #b89b68;
    --gold-text: #c2a46c;
    --white: #ffffff;
    --text-light: #e6e6e6;
    --text-dark: #1b1b1b;
    --rule: #4a4a4a;
    --rule-light: #888888;
    --social-a: #3566b0;
    --social-b: #1ea0e0;
    --social-c: #1f2d6a;
  }
  * { box-sizing: border-box; margin: 0; padding: 0; }
  html, body { width: 1200px; height: 2655px; overflow: hidden; background: var(--ink-dark); }
  body { position: relative; font-family: "PT Sans", Arial, sans-serif; color: var(--text-light); }
  .abs { position: absolute; }

  /* Hero */
  .hero { left: 0; top: 0; width: 1200px; height: 672px;
    background: linear-gradient(90deg, #161616 0%, #1d1d1d 40%, #2a2a2a 70%, #1c1c1c 100%); }
  .hero-photo { left: 566px; top: 0; width: 567px; height: 672px;
    background: radial-gradient(ellipse at 45% 30%, #4a4240 0%, #2a2624 35%, #121212 75%, #1a1a1a 100%); }
  .hero-name { left: 195px; top: 205px; font-family: "Fjalla One", Impact, sans-serif; font-weight: 400; font-size: 52px; line-height: 62px; color: var(--gold-text); letter-spacing: 1px; }
  .hero-role { left: 195px; top: 270px; font-size: 21px; color: var(--white); }
  .hero-button { left: 194px; top: 330px; width: 118px; height: 39px; border: 2px solid var(--white); border-radius: 20px;
    color: var(--white); font-size: 14px; display: flex; align-items: center; justify-content: center; }
  .menu-toggle { left: 1132px; top: 20px; width: 34px; height: 34px; border-radius: 50%; background: #4a4a4a; }

  /* Section headings */
  .section-title { left: 0; width: 1200px; text-align: center; font-family: "Montserrat", Arial, sans-serif; font-weight: 700; font-size: 25px; color: var(--gold-text); letter-spacing: 0.5px; }
  .section-rule { width: 1px; }
  .section-dot { width: 10px; height: 10px; border-radius: 50%; }

  /* About */
  .about-text { left: 375px; top: 870px; width: 450px; text-align: center; font-size: 14px; line-height: 20px; color: var(--text-light); }
  .about-signature { left: 0; top: 1005px; width: 1200px; text-align: center; font-family: "Dancing Script", cursive; font-size: 32px; color: var(--gold-text); }

  /* Work */
  .work-divide { left: 0; top: 1390px; }
  .work-title { left: 209px; top: 1137px; font-family: "Montserrat", Arial, sans-serif; font-weight: 700; font-size: 23px; color: var(--gold-text); }
  .work-text { left: 209px; top: 1188px; width: 255px; font-size: 11.5px; line-height: 17px; color: var(--text-light); }
  .work-list { left: 209px; top: 1256px; width: 230px; list-style: none; }
  .work-list li { height: 41.5px; display: flex; align-items: center; gap: 14px; border-bottom: 1px solid var(--rule);
    font-family: "Montserrat", Arial, sans-serif; font-weight: 500; font-size: 13px; color: var(--white); padding-left: 4px; }
  .work-list li:last-child { border-bottom: none; }
  .work-list svg { width: 16px; height: 16px; flex: none; }
  .work-tile { width: 212px; height: 183px; }
  .tile-library { left: 600px; top: 1135px; background: linear-gradient(180deg, #3e86c8 0%, #9c8a5a 60%, #4c6a34 100%); }
  .tile-gala { left: 834px; top: 1135px; background: linear-gradient(160deg, #d9a6e8 0%, #8d4fc7 55%, #4a2c8a 100%); }
  .tile-fair { left: 600px; top: 1336px; background: linear-gradient(180deg, #2d5fa4 0%, #c48a4a 55%, #3a2e38 100%); }
  .tile-towers { left: 834px; top: 1336px; background: linear-gradient(200deg, #dfefff 0%, #4f9be0 45%, #123e78 100%); }

  /* Services */
  .services-bg { left: 0; top: 1575px; width: 1200px; height: 392px; background: var(--white); }
  .services-title { top: 1596px; }
  .services-text { left: 415px; top: 1740px; width: 370px; text-align: center; font-size: 13px; line-height: 18.5px; color: var(--text-dark); }
  .services-list { left: 0; top: 1838px; width: 1200px; list-style: none; text-align: center; font-weight: 700; font-size: 13.5px; line-height: 24px; color: var(--text-dark); }

  /* Portrait band */
  .portrait-band { left: 0; top: 1967px; width: 1200px; height: 515px;
    background: radial-gradient(ellipse at 50% 45%, #2c2c2c 0%, #1e1e1e 45%, #161616 100%); }
  .portrait-photo { left: 400px; top: 1990px; width: 395px; height: 492px;
    background: radial-gradient(ellipse at 50% 25%, #5a4a42 0%, #262225 40%, #141418 75%, rgba(20,20,24,0) 100%); }

  /* Footer */
  .footer { left: 0; top: 2482px; width: 1200px; height: 173px; background: var(--gold); text-align: center; }
  .footer-title { left: 0; top: 27px; width: 1200px; font-family: "Montserrat", Arial, sans-serif; font-weight: 700; font-size: 14px; color: var(--white); }
  .social-link { top: 62px; width: 32px; height: 32px; border-radius: 50%; }
  .social-a { left: 545px; background: var(--social-a); }
  .social-b { left: 586px; background: var(--social-b); }
  .social-c { left: 626px; background: var(--social-c); }
  .footer-copy { left: 0; top: 130px; width: 1200px; font-size: 10.5px; color: var(--white); }
</style>
</head>
<body>

<header class="abs hero">
  <div class="abs hero-photo" role="img" aria-label="Portrait of the hypnotist in a dark shirt against a grey studio backdrop"></div>
  <h1 class="abs hero-name">Gareth Munroe</h1>
  <p class="abs hero-role">Stage Hypnotist</p>
  <a class="abs hero-button">Read More</a>
  <div class="abs menu-toggle" aria-label="Menu">
    <svg width="34" height="34" viewBox="0 0 34 34"><g stroke="#fff" stroke-width="1.6"><line x1="12" y1="13" x2="22" y2="13"/><line x1="12" y1="17" x2="22" y2="17"/><line x1="12" y1="21" x2="22" y2="21"/></g></svg>
  </div>
</header>

<section class="about">
  <h2 class="abs section-title" style="top:720px">ABOUT ME</h2>
  <div class="abs section-rule" style="left:600px;top:770px;height:67px;background:var(--rule-light)"></div>
  <div class="abs section-dot" style="left:595px;top:797px;background:var(--white)"></div>
  <p class="abs about-text">There are many variations of passages of Lorem Ipsum available, but the majority have suffered alteration in some form, by injected humour, or randomised words which don't look even slightly believable. If you are going to use a passage of Lorem Ipsum, you need to be sure there isn't anything embarrassing&nbsp; hidden&nbsp; in the middle of text.</p>
  <p class="abs about-signature">Gareth Munroe</p>
</section>

<section class="work">
  <svg class="abs work-divide" width="1200" height="200" viewBox="0 0 1200 200"><polygon points="0,191 1200,5 1200,200 0,200" fill="#ffffff"/></svg>
  <div class="abs section-rule" style="left:168px;top:1147px;height:67px;background:var(--rule-light)"></div>
  <div class="abs section-dot" style="left:163px;top:1174px;background:var(--white)"></div>
  <h2 class="abs work-title">My Work</h2>
  <p class="abs work-text">There are many variations of passages of Lorem Ipsum available, but the majority have suffered alteration in some form, by injected.</p>
  <ul class="abs work-list">
    <li><svg viewBox="0 0 16 16" fill="#fff"><polygon points="8,1 15,5 1,5"/><rect x="2" y="6" width="2" height="6"/><rect x="7" y="6" width="2" height="6"/><rect x="12" y="6" width="2" height="6"/><rect x="1" y="13" width="14" height="2"/></svg>High school shows</li>
    <li><svg viewBox="0 0 16 16" fill="#fff"><polygon points="8,3 16,7 8,11 0,7"/><path d="M3 9v3c2 2 8 2 10 0V9l-5 2.5z"/></svg>College</li>
    <li><svg viewBox="0 0 16 16" fill="#fff"><rect x="3" y="1" width="10" height="14"/><rect x="5" y="3" width="2" height="2" fill="#1b1b1b"/><rect x="9" y="3" width="2" height="2" fill="#1b1b1b"/><rect x="5" y="7" width="2" height="2" fill="#1b1b1b"/><rect x="9" y="7" width="2" height="2" fill="#1b1b1b"/></svg>Corporate</li>
    <li><svg viewBox="0 0 16 16" fill="none" stroke="#fff" stroke-width="1.6"><circle cx="8" cy="10" r="5"/><polygon points="6,1 10,1 11,3 8,5 5,3" fill="#fff"/></svg>Weddings</li>
    <li><svg viewBox="0 0 16 16" fill="none" stroke="#fff" stroke-width="1.5"><polyline points="1,2 1,15 15,15"/><polyline points="3,12 7,7 10,10 15,4"/></svg>Fundraisers</li>
    <li><svg viewBox="0 0 16 16" fill="#fff"><circle cx="5" cy="5" r="2.5"/><circle cx="11" cy="5" r="2.5"/><path d="M0 13c0-4 10-4 10 0z"/><path d="M7 13c0-4 9-4 9 0z"/></svg>Fairs</li>
  </ul>
  <div class="abs work-tile tile-library" role="img" aria-label="Domed university library under a blue sky"></div>
  <div class="abs work-tile tile-gala" role="img" aria-label="Banquet hall lit in purple for an evening event"></div>
  <div class="abs work-tile tile-fair" role="img" aria-label="Street fair with bunting at dusk"></div>
  <div class="abs work-tile tile-towers" role="img" aria-label="Glass office towers seen from below"></div>
</section>

<section class="services">
  <div class="abs services-bg"></div>
  <h2 class="abs section-title services-title">SERVICES</h2>
  <div class="abs section-rule" style="left:600px;top:1648px;height:67px;background:var(--text-dark)"></div>
  <div class="abs section-dot" style="left:595px;top:1673px;background:var(--text-dark)"></div>
  <p class="abs services-text">There are many variations of passages of Lorem Ipsum available, but the majority have suffered alteration in some form, by injected humour, or randomised&nbsp; which don't look even slightly believable.</p>
  <ul class="abs services-list">
    <li>Lorem Ipsum is simply dummy</li>
    <li>There are many variations</li>
    <li>It is a long established</li>
    <li>Contrary to popular</li>
  </ul>
</section>

<section class="abs portrait-band"></section>
<div class="abs portrait-photo" role="img" aria-label="Full-length portrait of the hypnotist in a dark shirt with braces"></div>

<footer class="abs footer">
  <p class="abs footer-title">Find me on Social Media</p>
  <a class="abs social-link social-a" aria-label="Social profile one"></a>
  <a class="abs social-link social-b" aria-label="Social profile two"></a>
  <a class="abs social-link social-c" aria-label="Social profile three"></a>
  <p class="abs footer-copy">Copyrights @ 2018 All Rights Reserved</p>
</footer>

</body>
</html>
```